Golf Brochure + Business Card Design Project – Kestrel Fitness.

Task Description

We are looking for a premium tri-fold brochure (8.5x11 letter, folded) plus a new business card design for Kestrel Fitness. Both need to look polished, elegant, and professional — something that would feel at home in a golf club environment.

Brochure Scope:
• Tri-fold brochure promoting our new golf-specific services
• Incorporate brand colors: deep hunter green, cream, and gold accents
• Clean, modern typography (professional, not playful)
• Layout will follow the copy provided (final copy attached, no rewriting needed)
• Imagery: mature golfers (50+), golf lifestyle shots, no generic stocky images
• Include QR code placement linking to booking page
• Deliverables: print-ready PDF with bleed/crop (CMYK), high-res PDF (digital), and source file (InDesign or Illustrator)

Business Card Scope:
• Front + back design
• Consistent with brand colors and fonts
• Space for name, title, phone, email, and website
• Deliverables: print-ready PDF with bleed/crop (CMYK) + source file (AI or InDesign)
• If possible, provide editable template for future staff cards

Timeline:
• First draft within 5–7 days
• 2 rounds of revisions included

Budget:
$300 USD (total for both brochure + business card)

I’ll provide finalized copy if you accept the project.
Project description (paste this whole block in that box)

We need a premium tri-fold brochure (8.5”×11” letter, folded) and a new business card design for Kestrel Fitness. This will be presented to golf course managers and members, so the look must be elegant, restrained, and country-club-classy.

Scope — Brochure
• Format: Tri-fold, 8.5”×11”. Please set 0.125” bleed on all sides and keep critical text ≥0.125–0.25” inside the trim.
• Purpose: Promote Kestrel Fitness’ golf-specific services for adults 50+.
• Copy: We will provide finalized copy in a Word doc after acceptance. No rewriting needed — please focus on layout and polish.
• Imagery (required):
• Golf-first images (ball on tee/green, mature golfers mid-swing, and golf course landscapes at golden hour).
• 1–2 real Kestrel Fitness gym photos on inside panels (trainer with client doing golf-relevant movement: stretch, rotation, balance).
• Visual style: Premium, quiet, lots of white/negative space, balanced grids; no clutter.
• Brand colors (required): Hunter Green #0C2E1F, Gold #CBA135, Cream #F5F2EB. Convert for CMYK print while preserving the look.
• Typography: Clean, legible serif + sans pairing (e.g., modern serif for headlines, humanist/neo-grotesk sans for body). You may propose suitable professional fonts; avoid playful/novelty fonts.
• Elements to include:
• Our logo (we will upload).
• QR code placement to booking page (we will supply the URL / QR asset).
• Simple icon treatment for the three complimentary options (Strength & Mobility, Stretch Therapy, Vitrascan + Assessment).
• Deliverables:
• Print-ready PDF (CMYK, with bleed & crop marks, PDF/X-1a or PDF/X-4)
• High-res digital PDF (no bleed)
• Source file (InDesign or Illustrator) + packaged fonts/links or outlined type as appropriate.

Scope — Business Card
• Size: 3.5”×2” (US standard) with 0.125” bleed; keep text ≥0.125” from trim.
• Front/back design; consistent with brochure branding.
• Fields: Name, Title, Phone, Email, Website, Address; optional small QR on back.
• Deliverables: Print-ready PDF (CMYK, bleed & crops) + Source file (AI/INDD). Provide an editable template for staff names.

Process & Timing
• Initial concept for brochure + card within 5–7 days of acceptance.
• 2 rounds of revisions included.
• Please start with a clean layout concept using placeholder images/text blocks; we’ll drop in final copy/assets immediately after acceptance.

Stock & Licensing
• You may propose stock images that fit the brief (we’re fine approving Pixelgrove or equivalent). Please note any license fees separately if needed.

Usage Rights
• We require full usage rights to the final designs for print & digital.

Target Market(s)

Golfers 50+ in Victoria, BC: quality-oriented, health-conscious, want to play longer, stronger, and pain-free. Country-club aesthetic; expect polished, professional materials.

Industry/Entity Type

Health & Fitness — Golf Performance / Longevity Studio

Font styles to use
Serif
Sans Serif

Requirements
Must have
• • Golf-first imagery + 1–2 real Kestrel Fitness photos inside. • Brand colors: #0C2E1F (Hunter Green), #CBA135 (Gold), #F5F2EB (Cream). • Premium, restrained layout; ample negative space; no clutter. • Clean professional serif + sans type pairing; highly legible. • Space for logo and QR code (booking). • Correct print specs (bleed, crops, CMYK). • Deliverables: print-ready PDFs (brochure + card), digital PDF, source files.
Nice to have
• • Subtle texture or grain in backgrounds (very light) to add sophistication. • A second brochure cover variation (ball on tee vs. course landscape) at concept stage.
Should not have
• • Cheesy/posed “stocky” groups; overly young models; beer/alcohol imagery. • Over-saturated greens/blues; gimmicky gradients or clip art. • Generic fitness/bodybuilding shots unrelated to golf performance.

```html
<!DOCTYPE html>
<html lang="en">
<head>
<meta charset="utf-8">
<title>Kestrel Fitness – Business Card Front and Back</title>
<link rel="stylesheet" href="https://fonts.googleapis.com/css2?family=Jost:wght@500;600;700&family=Oswald:wght@500&display=swap">
<style>
  :root {
    --backdrop: #2a2a2a;
    --cream: #fdfbd4;
    --hunter: #0c3333;
    --gold: #cba135;
    --gold-light: #e2c772;
    --rule: #9a9a8a;
  }
  * { box-sizing: border-box; margin: 0; padding: 0; }
  html, body {
    width: 1200px; height: 1108px; overflow: hidden;
    background: var(--backdrop);
  }
  .stage {
    width: 1200px; height: 1108px;
    display: flex; justify-content: center; align-items: center; gap: 60px;
  }
  .card {
    position: relative;
    width: 420px; height: 735px;
    border-radius: 22px;
    overflow: hidden;
    font-family: "Jost", sans-serif;
    text-transform: uppercase;
    box-shadow: 0 14px 30px rgba(0,0,0,.45);
  }
  .card--front { background: var(--cream); color: var(--hunter); }
  .card--back { background: var(--hunter); color: var(--gold); }

  .brand {
    position: absolute; left: 0; right: 0; top: 70px;
    display: flex; flex-direction: column; align-items: center; gap: 26px;
  }
  .brand__circle {
    width: 170px; height: 170px; border-radius: 50%;
    border: 4px solid currentColor;
  }
  .brand__name {
    font-weight: 600; font-size: 34px; letter-spacing: 9px; text-align: center;
    line-height: 1.25;
  }
  .card--back .brand { top: 150px; }
  .card--back .brand__circle { border-color: var(--gold); }

  .identity { position: absolute; left: 0; right: 0; top: 408px; text-align: center; }
  .identity__name { font-weight: 700; font-size: 29px; letter-spacing: .5px; }
  .identity__title { font-weight: 600; font-size: 16px; letter-spacing: 1px; margin-top: 6px; }

  .contact-icons {
    position: absolute; left: 40px; right: 40px; top: 506px;
    display: flex; align-items: center; gap: 10px;
  }
  .contact-icons__rule { flex: 1; height: 1px; background: var(--rule); }
  .contact-icons__item {
    width: 34px; height: 34px; border-radius: 6px; background: var(--hunter);
    display: flex; align-items: center; justify-content: center;
  }

  .contact-list {
    position: absolute; left: 0; right: 0; top: 560px;
    text-align: center; font-weight: 600; font-size: 16px; line-height: 1.75;
    letter-spacing: .3px;
  }
  .contact-list__phone { font-size: 18px; }

  .gold-tab {
    position: absolute; bottom: 0; left: 50%; transform: translateX(-50%);
    width: 150px; height: 18px;
    background: linear-gradient(90deg, var(--gold), var(--gold-light) 50%, var(--gold));
  }

  .tagline {
    position: absolute; left: 0; right: 0; bottom: 110px;
    text-align: center; font-family: "Oswald", sans-serif; font-weight: 500;
    font-size: 25px; letter-spacing: .5px; color: var(--gold);
  }
</style>
</head>
<body>
<main class="stage">
  <section class="card card--front" aria-label="Business card front">
    <div class="brand">
      <div class="brand__circle"></div>
      <div class="brand__name">Kestrel<br>Fitness</div>
    </div>
    <div class="identity">
      <h1 class="identity__name">Maren-Louise Ashby</h1>
      <p class="identity__title">Owner | Kestrel Fitness</p>
    </div>
    <div class="contact-icons">
      <span class="contact-icons__rule"></span>
      <span class="contact-icons__item" aria-label="Phone">
        <svg width="20" height="20" viewBox="0 0 24 24"><path fill="#fdfbd4" d="M6.6 10.8a15 15 0 0 0 6.6 6.6l2.2-2.2a1 1 0 0 1 1-.25 11 11 0 0 0 3.6.6 1 1 0 0 1 1 1V20a1 1 0 0 1-1 1A17 17 0 0 1 3 4a1 1 0 0 1 1-1h3.5a1 1 0 0 1 1 1 11 11 0 0 0 .6 3.6 1 1 0 0 1-.25 1z"/></svg>
      </span>
      <span class="contact-icons__item" aria-label="Email">
        <svg width="22" height="18" viewBox="0 0 24 18"><rect x="1.5" y="1.5" width="21" height="15" fill="none" stroke="#fdfbd4" stroke-width="2"/><path d="M1.5 1.5 12 10l10.5-8.5M1.5 16.5 9 8.5M22.5 16.5 15 8.5" fill="none" stroke="#fdfbd4" stroke-width="1.6"/></svg>
      </span>
      <span class="contact-icons__item" aria-label="Website">
        <svg width="20" height="20" viewBox="0 0 24 24"><circle cx="12" cy="12" r="9.5" fill="none" stroke="#fdfbd4" stroke-width="2"/><path d="M2.5 12h19M12 2.5c3 3 3 16 0 19M12 2.5c-3 3-3 16 0 19" fill="none" stroke="#fdfbd4" stroke-width="1.5"/></svg>
      </span>
      <span class="contact-icons__rule"></span>
    </div>
    <div class="contact-list">
      <p class="contact-list__phone">250-555-0148</p>
      <p>maren-louise@kestrelfitness.biz</p>
      <p>kestrelfitnessvictoria.com</p>
    </div>
    <span class="gold-tab"></span>
  </section>

  <section class="card card--back" aria-label="Business card back">
    <div class="brand">
      <div class="brand__circle"></div>
      <div class="brand__name">Kestrel<br>Fitness</div>
    </div>
    <p class="tagline">Strength • Mobility • Longevity</p>
    <span class="gold-tab"></span>
  </section>
</main>
</body>
</html>
```